AMBER AND SLATE WEB

We need a home design in wordpress, we have now a web but we would like to improve it. Our current web is www.amberandslatevillas.example Our business is holliday rental of villas in Ibiza. Our guest must know that we are a reliable company, professional and with experience and good reviews. We want them to click in our reservation engine: https://bookings.amberandslatevillas.example/en/ and make reservation in our website. We would also like to say that all the properties that we have are just us who commercialize so we have best price available. Many people are going to see our villas in staylist.example and look to our website to make a reservation with us so we need to show them that they are at the right place and click at our link to our reservation engine. What make us special is that we are a local company, we are from Ibiza, Our guests are always received in person by the Amber and Slate Ibiza team. You will enjoy extensive tourist information when you check in and during the entire stay. You will be attended by ChatterLine and calls, always happy to help so that you have a happy and fun stay! Our guest stay is better than in hotel as they have more spece, private swiming pool, private garden, barbeque ... To rent a villa is the best way to stay in Ibiza. We also have a promotional video: https://vidshare.example/Qm7TzR2pLxA Let our philosophy be shown, we think that coming on holiday to Ibiza implies seeing the nature that we have in Ibiza, hence our name AMBER AND SLATE, like the pins that almost touch the sea in Ibiza, or the posidonea meadows where the intense green of the seaweed and the blue of the sea. We are aware of the environment, and we love Ibiza. For us, the client who visits Ibiza, should rent a car, go around the island, eat in a restaurant one day in front of the sea, is a night of partying to the discs, go shopping, visit the ancient heritage of Umanity, make some aquatic sport, enjoy the pool, those are for us Ibiza.

Target Market(s)

Europe, people from Holand, UK, Germany, France, Spain ...

Industry/Entity Type

Tourism

Colors

Designer to choose colors to be used in the design.

Requirements
Must have
• Pictures of Ibiza.
Nice to have
• Our name Amber and Slate Ibiza is beacuse in Ibiza there is forest that almost touch the watter of the Mediterranean sea, so you can see green of the forest and blue of the sea and the sky. And also beacause under the watter of the sea there is a plant called Posidonia that is also green please see the picture of posidonia.

```html
<!DOCTYPE html>
<html lang="en">
<head>
<meta charset="utf-8">
<title>Amber and Slate Ibiza – Villas</title>
<link rel="stylesheet" href="https://fonts.googleapis.com/css2?family=Cinzel:wght@400;600&family=EB+Garamond:wght@600;700&family=Jost:wght@400;500&display=swap">
<style>
:root{
  --green:#5e7f34;
  --green-head:#6a8d37;
  --blue:#2a9fd6;
  --blue-dark:#1d6f9e;
  --ink:#3a3a3a;
  --muted:#6a6a6a;
  --line:#e2e2e2;
  --paper:#ffffff;
  --soft:#f4f4f4;
  --star:#e3a93b;
}
*{box-sizing:border-box;margin:0;padding:0}
html,body{width:1200px;height:4399px;overflow:hidden}
body{position:relative;background:var(--paper);font-family:"Jost",Arial,sans-serif;color:var(--ink)}
.abs{position:absolute}
.caps{font-family:"Cinzel",Georgia,serif;font-variant:small-caps}
.btn{position:absolute;display:flex;align-items:center;justify-content:center;background:var(--green);color:#fff;font-family:"Cinzel",Georgia,serif;font-size:14px;letter-spacing:1px}
.section-title{position:absolute;left:0;width:1200px;text-align:center;font-family:"Cinzel",Georgia,serif;font-size:31px;color:var(--green-head);letter-spacing:1px}
.section-title .accent{color:var(--blue)}

/* header */
.topline{left:0;top:0;width:1200px;height:4px;background:linear-gradient(90deg,var(--green),var(--blue))}
.brand{display:flex;align-items:center;gap:10px;font-family:"Cinzel",Georgia,serif;font-size:21px;color:var(--green-head)}
.brand .dot{width:14px;height:14px;border-radius:50%;background:var(--green-head)}
.nav{top:58px;font-family:"Cinzel",Georgia,serif;font-size:13px;letter-spacing:.5px;color:#333}
.nav.active{color:var(--green-head)}
.btn-blue{background:var(--blue)}

/* hero */
.hero{left:0;top:106px;width:1200px;height:500px;background:linear-gradient(160deg,#2f6b54 0%,#1f6f9a 30%,#1b5f8e 55%,#2da6c4 75%,#c9c2a1 100%)}
.hero-title{left:0;top:266px;width:1200px;text-align:center;font-family:"EB Garamond",Georgia,serif;font-weight:700;font-size:56px;line-height:64px;color:#fff}
.search{left:142px;top:563px;width:916px;height:97px;background:#fff;box-shadow:0 4px 14px rgba(0,0,0,.15)}
.s-label{top:18px;font-size:12.5px;color:#555}
.s-field{top:41px;height:38px;border:1px solid #ddd;display:flex;align-items:center;gap:8px;padding-left:10px;font-size:11.5px;color:#777}
.s-field svg{flex:none}

/* about */
.about{left:0;top:734px;width:1200px;height:369px;background:linear-gradient(180deg,#f6f8f2 0%,#eef3ea 60%,#d9ecf2 100%)}
.about-head{top:46px;left:0;width:1200px;display:flex;justify-content:center;align-items:center;gap:14px}
.about-head .word{font-family:"Cinzel",Georgia,serif;font-size:25px;color:var(--green-head)}
.about p{position:absolute;left:166px;width:867px;text-align:center;font-size:13px;line-height:22px;color:#444}

/* amenities */
.amen{left:142px;top:1248px;width:916px;height:358px;background:#fff}
.amen-photo{left:0;top:0;width:428px;height:358px;background:linear-gradient(170deg,#2c7fd1 0%,#6fb0e4 35%,#8b9b6e 60%,#c9c4b5 100%)}
.amen-item{display:flex;align-items:center;gap:9px;font-size:13.5px;color:#333}
.amen-rule{left:428px;width:488px;height:1px;background:var(--line)}
.amen-book{left:428px;top:305px;width:488px;height:53px;font-size:17px}

/* videos */
.videos{left:0;top:1693px;width:1200px;height:393px;background:linear-gradient(180deg,#2b2d2f,#3b3a37 60%,#2c3a44)}
.video-frame{left:288px;top:1895px;width:624px;height:382px;background:#fff;border:1px solid #ddd;padding:7px}
.video-frame .shot{width:100%;height:100%;background:linear-gradient(180deg,#3f86c8 0%,#8cb6d9 30%,#e6e3da 55%,#3aa0c7 75%,#2a7fb0 100%);display:flex;align-items:center;justify-content:center}
.arrow-btn{width:45px;height:45px;background:var(--blue);display:flex;align-items:center;justify-content:center}

/* gallery */
.tile{position:absolute}
.tile-hover{background:rgba(42,159,214,.85);color:#fff;display:flex;flex-direction:column;align-items:center;justify-content:center;text-align:center;font-size:14px;line-height:20px}

/* cta */
.cta{left:0;top:2986px;width:1200px;height:288px;background:linear-gradient(180deg,#1e4f73 0%,#1a5d86 55%,#15405f 100%)}
.cta-title{left:0;top:58px;width:1200px;text-align:center;font-family:"Cinzel",Georgia,serif;font-size:30px;line-height:37px;color:#fff;letter-spacing:1px}

/* testimonials */
.card{top:3419px;width:294px;height:186px;border:1px solid #ddd;background:#fff}
.card .avatar{position:absolute;left:16px;top:16px;width:66px;height:66px;border-radius:50%;background:linear-gradient(180deg,#9a8b7c,#4b4f57)}
.card .name{position:absolute;left:98px;top:36px;font-family:"Cinzel",Georgia,serif;font-size:12px;font-weight:600;color:#222}
.card .role{position:absolute;left:98px;top:52px;font-size:11px;color:#555}
.card .stars{position:absolute;left:16px;top:92px;display:flex;gap:3px}
.card .quote{position:absolute;left:16px;top:110px;width:266px;font-size:11px;line-height:17px;color:#555}

/* newsletter */
.news{left:0;top:3749px;width:1200px;height:339px;background:linear-gradient(100deg,#1f6aa0 0%,#2a8a9a 45%,#6ab34a 80%,#8cc63f 100%)}
.news-art{left:632px;top:126px;width:495px;height:196px;background:radial-gradient(ellipse at 35% 100%,rgba(247,196,0,.9) 0%,rgba(247,196,0,.6) 35%,rgba(255,255,255,0) 60%)}

/* footer */
.footer{left:0;top:4088px;width:1200px;height:262px;background:var(--soft)}
.f-head{font-family:"Cinzel",Georgia,serif;font-size:12.5px;color:#333;letter-spacing:.5px}
.f-link{font-size:12.5px;color:#444}
.f-link::before{content:"»";margin-right:10px;color:#888}
.f-text{font-size:12.5px;color:#444;line-height:18px}
.social{width:22px;height:22px}
.copy{left:0;top:4350px;width:1200px;height:49px;background:linear-gradient(90deg,#5e7f34,#3f8f9a 60%,#2a9fd6);color:#fff;font-size:12.5px;display:flex;align-items:center;justify-content:center}
</style>
</head>
<body>

<!-- header -->
<div class="abs topline"></div>
<div class="abs brand" style="left:70px;top:52px"><span class="dot"></span>Amber and Slate</div>
<div class="abs nav active" style="left:415px">Home</div>
<div class="abs nav" style="left:481px">Experience</div>
<div class="abs nav" style="left:585px">About us</div>
<div class="abs nav" style="left:677px">Contact Us</div>
<div class="btn btn-blue" style="left:787px;top:50px;width:143px;height:37px;font-size:12px">All properties</div>
<div class="btn" style="left:951px;top:50px;width:118px;height:37px;font-size:13px">Book Now</div>
<div class="abs" role="img" aria-label="Language flag" style="left:1089px;top:61px;width:27px;height:16px;background:linear-gradient(180deg,#b22234 0 50%,#f4f4f4 50% 100%);border:1px solid #ccc"></div>
<svg class="abs" style="left:1119px;top:66px" width="8" height="6" viewBox="0 0 8 6"><path d="M0 0h8L4 6z" fill="#333"/></svg>

<!-- hero -->
<div class="abs hero" role="img" aria-label="Photo of an Ibiza cove with pine-covered cliffs, turquoise water and sailing boats"></div>
<div class="abs hero-title">The Best Way To Stay<br>In Ibiza!</div>

<div class="abs search">
  <div class="abs s-label" style="left:36px">Check-in and check-out date:</div>
  <div class="abs s-field" style="left:36px;width:264px">
    <svg width="16" height="16" viewBox="0 0 16 16"><rect x="1" y="3" width="14" height="12" fill="none" stroke="#2a9fd6"/><path d="M1 6h14M5 1v4M11 1v4" stroke="#2a9fd6"/></svg>Select dates for your stay</div>
  <div class="abs s-label" style="left:312px">Nights:</div>
  <div class="abs s-field" style="left:312px;width:65px;justify-content:space-between;padding-right:8px">1
    <svg width="7" height="12" viewBox="0 0 7 12"><path d="M0 5L3.5 1 7 5zM0 7l3.5 4L7 7z" fill="#2a9fd6"/></svg></div>
  <div class="abs s-label" style="left:391px">No. of guests and rooms:</div>
  <div class="abs s-field" style="left:391px;width:186px">
    <svg width="18" height="14" viewBox="0 0 18 14"><circle cx="6" cy="4" r="3" fill="#2a9fd6"/><circle cx="13" cy="4" r="3" fill="#2a9fd6"/><path d="M0 14c0-4 3-6 6-6s6 2 6 6zM10 14c0-3 1-5 3-5s5 2 5 5z" fill="#2a9fd6"/></svg>2 adults (1 room)</div>
  <div class="abs s-label" style="left:589px">Promo Code:</div>
  <div class="abs s-field" style="left:589px;width:155px">
    <svg width="16" height="16" viewBox="0 0 16 16"><rect x="1" y="6" width="14" height="9" fill="none" stroke="#2a9fd6"/><rect x="0.5" y="3" width="15" height="3" fill="none" stroke="#2a9fd6"/><path d="M8 3v12" stroke="#2a9fd6"/></svg>Promo</div>
  <div class="btn" style="left:756px;top:41px;width:123px;height:38px;font-size:13px;gap:8px">
    <svg width="12" height="12" viewBox="0 0 12 12"><circle cx="5" cy="5" r="3.6" fill="none" stroke="#fff" stroke-width="1.8"/><path d="M7.6 7.6L11 11" stroke="#fff" stroke-width="2"/></svg>Search</div>
</div>

<!-- about -->
<div class="abs about" role="img" aria-label="Faded beach photo with umbrellas and swimmers behind the about text">
  <div class="abs about-head"><span class="word">About</span><span class="brand"><span class="dot"></span>Amber and Slate</span></div>
  <p style="top:104px">Amber and Slate Ibiza is a company specialized in offering its clients accommodation in Villas on the countryside of Ibiza. Our guests enjoy the rural Ibiza, tranquility, relax, private pool, close to dream beaches and coves, the best restaurants, an unforgettable holiday for family or friends.</p>
  <p style="top:158px">Every day can be a different experience, beach, restaurant, flea market, disco, hiking, kayaking, horseback riding, shopping, history, boat ride! There is a lot of variety for all budgets!The maximum distances of the island are 41 kilometers from north to south and 15 kilometers from east to west, we always recommend renting a car. Enjoy the freedom to go where you prefer, without depending on schedules or public transportation.</p>
  <div class="btn" style="left:541px;top:249px;width:116px;height:36px;font-size:13px">Read More</div>
</div>

<!-- amenities -->
<div class="section-title" style="top:1178px">Our <span class="accent">Amenities</span></div>
<div class="abs amen">
  <div class="abs amen-photo" role="img" aria-label="Photo of a villa pool terrace with white sun loungers under a blue sky"></div>
  <div class="abs amen-item" style="left:456px;top:52px"><svg width="24" height="20" viewBox="0 0 24 20" fill="none" stroke="#2a9fd6" stroke-width="1.4"><path d="M2 12l3-7h14l3 7v5H2z"/><path d="M2 12h20"/><circle cx="6" cy="15" r="1.3"/><circle cx="18" cy="15" r="1.3"/></svg>Rent A Car</div>
  <div class="abs amen-item" style="left:621px;top:52px"><svg width="24" height="22" viewBox="0 0 24 22" fill="none" stroke="#2a9fd6" stroke-width="1.4"><path d="M12 21V6M12 6C8 2 3 4 2 7M12 6c4-4 9-2 10 1M12 6C9 6 6 9 6 11M12 6c3 0 6 3 6 5M6 21h12"/></svg>Go Around The Island</div>
  <div class="abs amen-rule" style="top:94px"></div>
  <div class="abs amen-item" style="left:456px;top:108px"><svg width="24" height="22" viewBox="0 0 24 22" fill="none" stroke="#2a9fd6" stroke-width="1.4"><path d="M4 7h16l-1 14H5z"/><path d="M8 9V5a4 4 0 018 0v4"/></svg>Go Shopping</div>
  <div class="abs amen-item" style="left:621px;top:108px"><svg width="28" height="22" viewBox="0 0 28 22" fill="none" stroke="#2a9fd6" stroke-width="1.4"><circle cx="14" cy="11" r="7"/><circle cx="14" cy="11" r="4"/><path d="M3 2v18M1 2v5h4V2M25 2v18M25 2c2 2 2 6 0 8"/></svg>Eat In A Restaurant</div>
  <div class="abs amen-rule" style="top:148px"></div>
  <div class="abs amen-item" style="left:456px;top:165px"><svg width="26" height="22" viewBox="0 0 26 22" fill="none" stroke="#2a9fd6" stroke-width="1.4"><circle cx="17" cy="4" r="2.5"/><path d="M5 12l6-6 5 4-6 4M1 18c3-2 5 2 8 0s5 2 8 0 5 2 8 0"/></svg>Aquatic Sport</div>
  <div class="abs amen-item" style="left:621px;top:165px"><svg width="24" height="24" viewBox="0 0 24 24" fill="none" stroke="#2a9fd6" stroke-width="1.4"><circle cx="12" cy="12" r="9"/><path d="M3 12h18M12 3c-4 4-4 14 0 18M12 3c4 4 4 14 0 18"/></svg>Night Of Partying To The Discos</div>
  <div class="abs amen-rule" style="top:208px"></div>
  <div class="abs amen-item" style="left:456px;top:225px"><svg width="26" height="24" viewBox="0 0 26 24" fill="none" stroke="#2a9fd6" stroke-width="1.4"><path d="M7 18V4a3 3 0 016 0M15 18V4a3 3 0 016 0M7 8h8M7 13h8M1 20c3-2 5 2 8 0s5 2 8 0 5 2 8 0"/></svg>Enjoy The Pool</div>
  <div class="abs amen-item" style="left:621px;top:225px"><svg width="24" height="26" viewBox="0 0 24 26" fill="none" stroke="#2a9fd6" stroke-width="1.4"><path d="M12 1l3 6H9zM7 7h10v3H7zM8 10v10M12 10v10M16 10v10M4 20h16v3H4zM2 23h20v2H2z"/></svg>Visit The Ancient Heritage Of Umanity</div>
  <div class="btn amen-book">Book Now</div>
</div>

<!-- videos -->
<div class="abs videos" role="img" aria-label="Dimmed photo of a villa pool at dusk"></div>
<div class="abs caps" style="left:0;top:1770px;width:1200px;text-align:center;font-size:30px;color:#fff;letter-spacing:1px">Watch Videos</div>
<div class="abs" style="left:250px;top:1814px;width:700px;text-align:center;font-size:14px;line-height:24px;color:#fff">Lorem ipsum dolor sit amet, consectetuer adipiscing elit, sed diam nonummy nibh euismod tincidunt ut laoreet dolore magna aliquam erat volutpat modo consequat.</div>
<div class="abs video-frame">
  <div class="shot" role="img" aria-label="Video still of a white Ibiza villa with a pool and sun loungers">
    <svg width="62" height="62" viewBox="0 0 62 62"><circle cx="31" cy="31" r="28" fill="rgba(255,255,255,.2)" stroke="#fff" stroke-width="3"/><path d="M25 19l19 12-19 12z" fill="#fff"/></svg>
  </div>
</div>
<div class="abs arrow-btn" style="left:242px;top:2064px"><svg width="12" height="16" viewBox="0 0 12 16"><path d="M9 2L3 8l6 6" fill="none" stroke="#fff" stroke-width="2.4"/></svg></div>
<div class="abs arrow-btn" style="left:912px;top:2064px"><svg width="12" height="16" viewBox="0 0 12 16"><path d="M3 2l6 6-6 6" fill="none" stroke="#fff" stroke-width="2.4"/></svg></div>

<!-- gallery -->
<div class="section-title" style="top:2356px">Our <span class="accent">Gallery</span></div>
<div class="tile" role="img" aria-label="White villa facade with palms" style="left:142px;top:2422px;width:220px;height:183px;background:linear-gradient(180deg,#4d8ed6,#e9e6df 50%,#5f7a3a)"></div>
<div class="tile" role="img" aria-label="Covered terrace with dining table" style="left:142px;top:2615px;width:220px;height:222px;background:linear-gradient(180deg,#8a5a38,#c79c72 35%,#d9d2c4 65%,#7d8b5a)"></div>
<div class="tile" role="img" aria-label="Pool among pine trees with loungers" style="left:372px;top:2422px;width:222px;height:244px;background:linear-gradient(180deg,#4c7a3c,#4fb0d8 50%,#d8d2c6)"></div>
<div class="tile" role="img" aria-label="Yellow villa with blue pool" style="left:372px;top:2675px;width:222px;height:162px;background:linear-gradient(180deg,#3a8ee0,#e0b84a 45%,#2b9ed4)"></div>
<div class="tile tile-hover" style="left:604px;top:2422px;width:222px;height:162px">
  <svg width="38" height="38" viewBox="0 0 38 38"><circle cx="19" cy="19" r="17" fill="none" stroke="#fff" stroke-width="1.5"/><path d="M19 11v16M11 19h16" stroke="#fff" stroke-width="1.5"/></svg>
  <div style="margin-top:10px;width:170px">Lorem ipsum dolor sit amet consectetuer</div>
</div>
<div class="tile" role="img" aria-label="Pool terrace facing a wooded hillside" style="left:604px;top:2594px;width:222px;height:243px;background:linear-gradient(180deg,#5a9bd6,#4f7a3d 35%,#2fb7e4 65%,#c9875a)"></div>
<div class="tile" role="img" aria-label="Living room with sofas and wooden furniture" style="left:836px;top:2422px;width:222px;height:244px;background:linear-gradient(180deg,#efe9df,#b57a45 45%,#3b4660 75%,#9a7556)"></div>
<div class="tile" role="img" aria-label="Villa pool under blue sky" style="left:836px;top:2675px;width:222px;height:162px;background:linear-gradient(180deg,#2f7fd8,#d9d4c9 45%,#1f9de0)"></div>
<div class="btn" style="left:541px;top:2864px;width:118px;height:38px;font-size:13px">View More</div>

<!-- cta -->
<div class="abs cta" role="img" aria-label="Bay of Ibiza with anchored sailing boats"></div>
<div class="abs cta-title" style="top:3056px">Villas And The Countryside<br>The Best Option To Stay In Ibiza</div>
<div class="btn" style="left:517px;top:3153px;width:166px;height:43px;font-size:16px">Book Now</div>

<!-- testimonials -->
<div class="section-title" style="top:3353px;color:var(--green-head)">Client <span class="accent">Testimonials</span></div>
<svg class="abs" style="left:94px;top:3485px" width="18" height="54" viewBox="0 0 18 54"><path d="M16 1L2 27l14 26" fill="none" stroke="#bbb" stroke-width="2"/></svg>
<svg class="abs" style="left:1088px;top:3485px" width="18" height="54" viewBox="0 0 18 54"><path d="M2 1l14 26L2 53" fill="none" stroke="#bbb" stroke-width="2"/></svg>

<div class="abs card" style="left:145px">
  <div class="avatar" role="img" aria-label="Portrait photo of the guest"></div>
  <div class="name">Marlo Vance</div><div class="role">Lorem ipsum dolor</div>
  <div class="stars"><svg width="66" height="11" viewBox="0 0 66 11"><g fill="none" stroke="#e3a93b"><path id="st" d="M5.5 .8l1.4 3 3.2.4-2.3 2.2.6 3.2-2.9-1.6-2.9 1.6.6-3.2L.9 4.2l3.2-.4z"/><use href="#st" x="13"/><use href="#st" x="26"/><use href="#st" x="39"/><use href="#st" x="52"/></g></svg></div>
  <div class="quote">Lorem ipsum dolor sit amet, consectetuer adipiscing elit, sed diam nonummy nibh euismod tincidunt ut laoreet dolore magna aliquam erat volutpat.</div>
</div>
<div class="abs card" style="left:457px">
  <div class="avatar" role="img" aria-label="Portrait photo of the guest"></div>
  <div class="name">Idris Kell</div><div class="role">Lorem ipsum dolor</div>
  <div class="stars"><svg width="66" height="11" viewBox="0 0 66 11"><g fill="none" stroke="#e3a93b"><use href="#st"/><use href="#st" x="13"/><use href="#st" x="26"/><use href="#st" x="39"/><use href="#st" x="52"/></g></svg></div>
  <div class="quote">Lorem ipsum dolor sit amet, consectetuer adipiscing elit, sed diam nonummy nibh euismod tincidunt ut laoreet dolore magna aliquam erat volutpat.</div>
</div>
<div class="abs card" style="left:768px">
  <div class="avatar" role="img" aria-label="Portrait photo of the guest"></div>
  <div class="name">Nora Fenn</div><div class="role">Lorem ipsum dolor</div>
  <div class="stars"><svg width="66" height="11" viewBox="0 0 66 11"><g fill="none" stroke="#e3a93b"><use href="#st"/><use href="#st" x="13"/><use href="#st" x="26"/><use href="#st" x="39"/><use href="#st" x="52"/></g></svg></div>
  <div class="quote">Lorem ipsum dolor sit amet, consectetuer adipiscing elit, sed diam nonummy nibh euismod tincidunt ut laoreet dolore magna aliquam erat volutpat.</div>
</div>
<div class="btn" style="left:539px;top:3631px;width:104px;height:36px;font-size:13px">View All</div>

<!-- newsletter -->
<div class="abs news">
  <div class="abs news-art" role="img" aria-label="Illustration of an aeroplane flying over a yellow sun and clouds"></div>
  <div class="abs caps" style="left:140px;top:80px;font-size:31px;color:#fff;letter-spacing:1px">Newsletter Sign Up</div>
  <div class="abs" style="left:140px;top:134px;width:430px;font-size:13.5px;line-height:24px;color:#fff">Lorem ipsum dolor sit amet, consectetuer adipiscing elit, sed diam nonummy nibh euismod tincidunt ut laoreet dolore magna aliquam erat volutpat modo consequat.</div>
  <div class="abs" style="left:140px;top:216px;width:277px;height:38px;background:#fff;display:flex;align-items:center;padding-left:16px;font-size:11px;color:#777">Enter your Email Address</div>
  <div class="btn" style="left:428px;top:216px;width:157px;height:38px;font-size:14px">Subscribe</div>
</div>

<!-- footer -->
<div class="abs footer">
  <div class="abs f-head" style="left:142px;top:66px">Quick Links</div>
  <div class="abs f-link" style="left:142px;top:94px">Home</div>
  <div class="abs f-link" style="left:142px;top:122px">Experience</div>
  <div class="abs f-link" style="left:142px;top:150px">About us</div>
  <div class="abs f-link" style="left:142px;top:178px">Contact Us</div>

  <div class="abs f-head" style="left:292px;top:66px">Contact Details</div>
  <svg class="abs" style="left:292px;top:95px" width="10" height="14" viewBox="0 0 10 14"><path d="M5 0a5 5 0 015 5c0 4-5 9-5 9S0 9 0 5a5 5 0 015-5z" fill="#333"/><circle cx="5" cy="5" r="1.8" fill="#f4f4f4"/></svg>
  <div class="abs f-head" style="left:310px;top:93px">Amber &amp; Slate</div>
  <div class="abs f-text" style="left:310px;top:111px;width:200px">123 Lorem ipsum dolor sit amet, consectetuer adipiscing elit.</div>
  <svg class="abs" style="left:292px;top:158px" width="12" height="12" viewBox="0 0 12 12"><path d="M2.5 0l2 3-1.2 1.5a7 7 0 004.2 4.2L9 7.5l3 2-1.5 2.5C5 12 0 7 0 1.5z" fill="#333"/></svg>
  <div class="abs f-text" style="left:310px;top:155px">+34 600 123 456</div>
  <svg class="abs" style="left:292px;top:190px" width="13" height="11" viewBox="0 0 13 11"><rect x=".5" y=".5" width="12" height="10" fill="none" stroke="#333"/><path d="M.5 .5l6 5 6-5" fill="none" stroke="#333"/></svg>
  <div class="abs f-text" style="left:310px;top:186px">reservas@amberandslatevillas.example</div>

  <div class="abs f-head" style="left:579px;top:66px">Location Map</div>
  <div class="abs" role="img" aria-label="Small road map of the villa location in Ibiza" style="left:579px;top:94px;width:218px;height:102px;background:linear-gradient(135deg,#eef0e6,#e2e6da 50%,#f1ece0);border:1px solid #ddd"></div>

  <div class="abs brand" style="left:866px;top:94px;font-size:18px"><span class="dot"></span>Amber and Slate</div>
  <div class="abs social" style="left:899px;top:164px;background:#3b5998"></div>
  <div class="abs social" style="left:930px;top:164px;background:#1da1f2"></div>
  <div class="abs social" style="left:960px;top:164px;background:#0077b5"></div>
  <div class="abs social" style="left:990px;top:164px;background:#a0785a"></div>
</div>
<div class="abs copy">Copyright © 2019 Amber &amp; Slate. All Rights Reserved.</div>

</body>
</html>
```